Steady Harbor: Receiving Plenty Without Price

Religious genre. 6x9 book cover design for a new book that will also eventually be made into a workbook. Summary: Learn how God created you to be part of His Story of Grace so that you can flourish in your new identity in Him. This book explores how the story of the gospel informs our stories, how to live a new and free life by utilizing the 3 dimensions of the Gospel, and overcome how our former life has dominated us.

Target Market(s)

church members, church leaders

Industry/Entity Type

Religion

Colors
ffffff

Requirements
Must have
• White background with red and black print, clean, not too busy, easy-to-read design and font choices
Nice to have
• Play off the idea of the word "Vital" ... like vital signs or vitality

```html
<!DOCTYPE html>
<html lang="en">
<head>
<meta charset="utf-8">
<title>Steady Harbor: Receiving Plenty Without Price — Cover Wrap</title>
<link rel="stylesheet" href="https://fonts.googleapis.com/css2?family=Anton&display=swap">
<style>
  :root {
    --page: #ffffff;
    --paper: #efefef;
    --paper-light: #f4f4f4;
    --ink: #111111;
    --red: #d0141a;
    --barcode-box: #ffffff;
    --heart-light: #fbfbfb;
    --heart-shade: #e2e2e2;
  }
  * { margin: 0; padding: 0; box-sizing: border-box; }
  html, body {
    width: 775px; height: 1200px; overflow: hidden;
    background: var(--page);
    font-family: "Anton", "Oswald", sans-serif;
    color: var(--ink);
  }
  .cover-wrap {
    position: absolute; left: 0; top: 320px;
    width: 775px; height: 561px;
    display: flex;
    background: var(--paper);
    overflow: hidden;
  }
  .small-caps { font-variant: small-caps; text-transform: none; }

  /* Back cover */
  .back-cover {
    position: relative; width: 370px; height: 100%;
    background: linear-gradient(160deg, var(--paper-light), var(--paper));
  }
  .back-cover .author {
    position: absolute; top: 36px; width: 100%; text-align: center;
    font-size: 21px; letter-spacing: 0.5px;
  }
  .back-cover .title {
    position: absolute; top: 64px; width: 100%; text-align: center;
    font-size: 32px; line-height: 1; color: var(--red); white-space: nowrap;
  }
  .back-cover .subtitle {
    position: absolute; top: 104px; width: 100%; text-align: center;
    font-size: 17px; line-height: 1.2; white-space: nowrap;
  }
  .back-cover .blurb {
    position: absolute; top: 222px; left: 38px; width: 298px;
    font-size: 13.6px; line-height: 22.4px; text-align: justify;
    text-align-last: center; text-indent: 22px; letter-spacing: 0.3px;
  }
  .back-cover .barcode-area {
    position: absolute; left: 234px; top: 463px;
    width: 121px; height: 73px; background: var(--barcode-box);
  }

  /* Spine */
  .spine {
    position: relative; width: 35px; height: 100%;
    background: var(--paper-light);
  }
  .spine .spine-text {
    position: absolute; left: 8px; top: 52px;
    writing-mode: vertical-rl;
    font-size: 17px; white-space: nowrap; line-height: 1;
  }
  .spine .spine-author { margin-bottom: 20px; display: inline-block; }
  .spine .spine-title { color: var(--red); }

  /* Front cover */
  .front-cover {
    position: relative; width: 370px; height: 100%;
    background: linear-gradient(200deg, var(--paper-light), var(--paper));
  }
  .front-cover .author {
    position: absolute; top: 16px; width: 100%; text-align: center;
    font-size: 34px; letter-spacing: 0.5px;
  }
  .front-cover .title {
    position: absolute; top: 78px; width: 100%; text-align: center;
    font-size: 52px; line-height: 1; color: var(--red); white-space: nowrap;
  }
  .front-cover .vital-art {
    position: absolute; left: 40px; top: 196px; width: 279px; height: 259px;
  }
  .front-cover .subtitle {
    position: absolute; top: 472px; width: 100%; text-align: center;
    font-size: 26px; white-space: nowrap;
  }
</style>
</head>
<body>
  <main class="cover-wrap">
    <section class="back-cover">
      <p class="author small-caps">Author name</p>
      <h2 class="title small-caps">Steady Harbor:</h2>
      <p class="subtitle small-caps">Receiving Plenty Without Price</p>
      <p class="blurb small-caps">Learn how God created you to be part of His Story of Grace so that you can flourish in your new identity in Him. This book explores how the story of the gospel informs our stories, how to live a new and free life by utilizing the 3 dimensions of the Gospel, and overcome how our former life has dominated us.</p>
      <div class="barcode-area"></div>
    </section>

    <section class="spine">
      <p class="spine-text small-caps">
        <span class="spine-author">Author name</span>
        <span class="spine-title">Steady Harbor:</span>
        <span class="spine-subtitle">Receiving Plenty Without Price</span>
      </p>
    </section>

    <section class="front-cover">
      <p class="author small-caps">Author name</p>
      <h1 class="title small-caps">Steady Harbor:</h1>
      <svg class="vital-art" viewBox="0 0 279 259" role="img" aria-label="Paper-cut white heart with a cross cut-out and a red heartbeat line running through it">
        <defs>
          <linearGradient id="heart-tone" x1="0" y1="0" x2="1" y2="1">
            <stop offset="0" stop-color="#fbfbfb"/>
            <stop offset="1" stop-color="#e2e2e2"/>
          </linearGradient>
        </defs>
        <rect width="279" height="259" rx="18" fill="url(#heart-tone)"/>
      </svg>
      <p class="subtitle small-caps">Receiving Plenty Without Price</p>
    </section>
  </main>
</body>
</html>
```